I need a flyer made , the flyer can be one page or two pages or three pages . I will be posting this on Instagram and social media platforms. I am a luxury home builder , I am looking to hire a construction project manager . Below are some examples and ideas what can be on the flyer

We’re looking for a construction project manager who’s passionate about building luxury homes at the highest standards
We’re hiring construction project manager
* Experience 5+ years in residential project management with a strong portfolio of completed homes.
* location : Bergen County NJ
* excellent leadership skills, leads teams with confidence and clarity
* communicates seamlessly with architects , engineers, designers and clients
*knows how to manage budgets and timelines without compromising quality
*solves problems with a positive solution first mindset
* pays attention to every detail because in luxury the small things are the big things

Apply now , link in bio or DM to connect.

My logo is attached, my web site www.velstridebuilders.com
My style is modern but still warm and inviting. I like a clean classy look .

Please don’t add any images of chairs or people to the flyer , I do not want people on my flyer. Do not add standard images of offices and houses , we are luxury builders , we build homes over 2 million dollars. Keep a classy , simple modern look . High end .

You can add a white hard hat with my logo on it for a image , this is a suggestion does not have to be on my flyer ,

```html
<!DOCTYPE html>
<html lang="en">
<head>
<meta charset="utf-8">
<title>Velstride Builders – Construction Project Manager</title>
<link rel="stylesheet" href="https://fonts.googleapis.com/css2?family=Tinos:wght@400&family=Roboto+Condensed:wght@300;400;700&family=Roboto:wght@900&display=swap">
<style>
  :root {
    --paper: #ffffff;
    --ink: #111111;
    --band: #000000;
    --accent: #e3262c;
    --muted: #7a7a7a;
    --light: #ffffff;
    --render-top: #f4f4f4;
    --render-mid: #a89684;
    --render-low: #e9ebec;
  }
  * { margin: 0; padding: 0; box-sizing: border-box; }
  html, body { width: 927px; height: 1200px; overflow: hidden; background: var(--paper); }
  .flyer { position: relative; width: 927px; height: 1200px; background: var(--paper); overflow: hidden; color: var(--ink); }

  .headline-intro {
    position: absolute; top: 40px; left: 0; width: 927px; text-align: center;
    font-family: "Tinos", "Times New Roman", serif; font-weight: 400; font-size: 60px; line-height: 1;
  }
  .headline-main {
    position: absolute; top: 118px; left: 0; width: 927px; text-align: center;
    font-family: "Tinos", "Times New Roman", serif; font-weight: 400; font-size: 172px; line-height: 1; letter-spacing: 1px;
  }
  .headline-spacer { visibility: hidden; }
  .headline-mark { position: absolute; top: 78px; left: 738px; width: 80px; height: 180px; }

  .home-render {
    position: absolute; top: 286px; left: 368px; width: 559px; height: 348px;
    background: radial-gradient(ellipse 70% 60% at 52% 48%, var(--render-mid) 0%, #c3b7aa 40%, var(--render-low) 75%, var(--render-top) 100%);
  }

  .brand-name {
    position: absolute; top: 412px; left: 61px;
    font-family: "Tinos", "Times New Roman", serif; font-weight: 400; font-size: 38px; line-height: 1; letter-spacing: 1px;
    text-transform: uppercase; white-space: nowrap;
  }
  .brand-tagline {
    position: absolute; top: 514px; left: 61px;
    font-family: "Tinos", "Times New Roman", serif; font-weight: 400; font-size: 26px; line-height: 1; letter-spacing: 0.5px;
    white-space: nowrap;
  }

  .info-band { position: absolute; top: 634px; left: 0; width: 927px; height: 566px; background: var(--band); color: var(--light); }
  .role-kicker {
    position: absolute; top: 26px; left: 0; width: 927px; text-align: center;
    font-family: "Tinos", "Times New Roman", serif; font-weight: 400; font-size: 33px; line-height: 1;
  }
  .role-title {
    position: absolute; top: 62px; left: 0; width: 927px; text-align: center;
    font-family: "Tinos", "Times New Roman", serif; font-weight: 400; font-size: 56px; line-height: 1;
  }
  .role-subtitle {
    position: absolute; top: 142px; left: 0; width: 927px; text-align: center;
    font-family: "Roboto Condensed", "Arial Narrow", sans-serif; font-weight: 300; font-size: 19px;
    color: var(--muted); text-transform: uppercase; letter-spacing: 0.3px;
  }
  .requirements { position: absolute; top: 180px; left: 54px; list-style: none; }
  .requirements li {
    position: relative; padding-left: 28px; height: 32px; line-height: 28px;
    font-family: "Roboto Condensed", "Arial Narrow", sans-serif; font-size: 18.5px; font-weight: 400;
  }
  .requirements li::before {
    content: ""; position: absolute; left: 0; top: 7px; width: 14px; height: 14px; border-radius: 50%; background: var(--light);
  }
  .requirements strong { font-weight: 700; }

  .apply-button { position: absolute; top: 454px; left: 33px; width: 296px; height: 66px; }
  .website {
    position: absolute; top: 475px; left: 368px;
    font-family: "Roboto Condensed", "Arial Narrow", sans-serif; font-size: 20px; letter-spacing: 4.4px;
    text-transform: uppercase;
  }
</style>
</head>
<body>
<main class="flyer">
  <p class="headline-intro">We’re</p>
  <h1 class="headline-main">HIRING<span class="headline-spacer">!</span></h1>
  <svg class="headline-mark" viewBox="0 0 80 180" aria-hidden="true">
    <path d="M54 4 L74 10 L34 128 L26 126 Z" fill="var(--accent)"/>
    <circle cx="24" cy="160" r="13" fill="var(--accent)"/>
  </svg>

  <div class="home-render" role="img" aria-label="Rendering of a modern luxury two-storey home with wood panelling, glass walls and landscaped trees"></div>

  <p class="brand-name">Velstride Builders</p>
  <p class="brand-tagline">PLAN. CRAFT. DELIVER.</p>

  <section class="info-band">
    <h2 class="role-kicker">CONSTRUCTION</h2>
    <h2 class="role-title">PROJECT MANAGER</h2>
    <p class="role-subtitle">Who’s passionate about building luxury homes at the highest standards</p>
    <ul class="requirements">
      <li>Experience 5+ years in residential project management with a strong portfolio of completed homes.</li>
      <li><strong>LOCATION</strong> : Bergen County NJ</li>
      <li>Excellent leadership skills, leads teams with confidence and clarity</li>
      <li>Communicates seamlessly with architects , engineers, designers and clients</li>
      <li>Knows how to manage budgets and timelines without compromising quality</li>
      <li>Solves problems with a positive solution first mindset</li>
      <li>Pays attention to every detail because in luxury the small things are the big things</li>
    </ul>

    <svg class="apply-button" viewBox="0 0 296 66" role="img" aria-label="Apply now">
      <rect x="0" y="0" width="168" height="66" rx="10" fill="var(--light)"/>
      <path d="M150 0 H284 Q296 0 296 12 V54 Q296 66 284 66 H150 L172 33 Z" fill="var(--accent)"/>
      <text x="12" y="46" font-family="Roboto, Arial, sans-serif" font-weight="900" font-size="34" fill="var(--ink)">APPLY</text>
      <text x="180" y="46" font-family="Roboto, Arial, sans-serif" font-weight="900" font-size="34" fill="var(--light)">NOW!</text>
    </svg>
    <p class="website">www.velstridebuilders.com</p>
  </section>
</main>
</body>
</html>
```